Law Offices business card

Hi there, I'll need business card for the Law Offices of Colin Matheny. The information must convey his strategic approach and quick resolution to complex business litigation needs. Please emphasize Civil Litigation, Corporate Law, Business Governance and Real Estate Law. Colin has over 25 years of experience in these fields.The card should be modern and edgy and the message should be clear. Please consult his current website for ideas.

```html
<!DOCTYPE html>
<html lang="en">
<head>
<meta charset="utf-8">
<title>Law Offices of Colin Matheny – Business Card</title>
<link rel="stylesheet" href="https://fonts.googleapis.com/css2?family=Oranienbaum&family=Source+Sans+3:wght@400;600;700&display=swap">
<style>
  :root {
    --orange: #fa6100;
    --white: #ffffff;
    --ink-grey: #4a4a4a;
    --soft-grey: #6b6b6b;
    --rule-grey: #bdbdbd;
    --backdrop: #e9e7e4;
    --card-shadow: rgba(0, 0, 0, 0.12);
  }
  * { margin: 0; padding: 0; box-sizing: border-box; }
  html, body { width: 1200px; height: 900px; overflow: hidden; }
  body {
    position: relative;
    background: var(--backdrop);
    font-family: "Source Sans 3", Arial, sans-serif;
  }
  .card {
    position: absolute;
    background: var(--white);
    box-shadow: 0 4px 14px var(--card-shadow);
    overflow: hidden;
  }

  /* Brand lockup */
  .brand { position: absolute; display: flex; align-items: center; }
  .brand-mark { border-radius: 50%; flex: none; }
  .brand-divider { width: 1px; align-self: stretch; }
  .brand-name {
    font-family: "Oranienbaum", "Times New Roman", serif;
    font-weight: 400; text-transform: uppercase; line-height: 1;
  }
  .brand-name .line-top, .brand-name .line-bottom { display: block; white-space: nowrap; }

  /* Front */
  .card-front { left: 78px; top: 34px; width: 588px; height: 364px; }
  .front-header { position: absolute; left: 0; top: 0; width: 100%; height: 143px; }
  .front-header .brand { left: 30px; top: 31px; height: 92px; }
  .front-header .brand-mark {
    width: 88px; height: 88px; border: 4px solid var(--ink-grey); background: var(--orange);
  }
  .front-header .brand-divider { background: var(--rule-grey); margin: 0 14px 0 16px; }
  .front-header .line-top { font-size: 38px; color: var(--orange); letter-spacing: 0.3px; }
  .front-header .line-bottom { font-size: 20px; color: var(--ink-grey); margin-top: 2px; }

  .front-body {
    position: absolute; left: 0; top: 143px; width: 100%; height: 221px;
    background: var(--orange); color: var(--white);
    padding: 21px 30px 0 30px;
  }
  .person-name { font-size: 22px; font-weight: 600; line-height: 1.15; }
  .person-role { font-size: 16px; line-height: 1.3; margin-bottom: 9px; }
  .contact-list { list-style: none; font-size: 16.5px; line-height: 24.5px; }
  .contact-list li { display: flex; align-items: center; white-space: nowrap; }
  .contact-list svg { width: 12px; height: 12px; margin-right: 7px; fill: var(--white); flex: none; }
  .contact-address { margin-top: 2px; }

  /* Back */
  .card-back { left: 388px; top: 505px; width: 567px; height: 352px; }
  .back-tagline {
    position: absolute; left: 0; top: 0; width: 100%; height: 110px;
    display: flex; align-items: center; justify-content: center;
    font-size: 17px; font-weight: 600; letter-spacing: 2px; text-transform: uppercase;
    color: var(--orange);
  }
  .back-band {
    position: absolute; left: 0; top: 110px; width: 100%; height: 131px;
    background: var(--orange);
  }
  .back-band .brand { left: 132px; top: 24px; height: 84px; }
  .back-band .brand-mark { width: 82px; height: 82px; border: 4px solid var(--white); }
  .back-band .brand-divider { background: var(--white); margin: 0 13px 0 15px; }
  .back-band .line-top { font-size: 36px; color: var(--white); letter-spacing: 0.3px; }
  .back-band .line-bottom { font-size: 19px; color: var(--white); margin-top: 2px; }
  .practice-areas {
    position: absolute; left: 0; top: 241px; width: 100%; height: 111px;
    display: flex; flex-wrap: wrap; align-content: center; justify-content: center;
    list-style: none; padding: 0 40px; row-gap: 4px;
    font-size: 15px; color: var(--soft-grey);
  }
  .practice-areas li { white-space: nowrap; }
  .practice-areas li + li::before { content: "|"; color: var(--orange); margin: 0 10px; }
  .practice-areas li:nth-child(3)::before { content: none; }
  .practice-areas li:nth-child(3) { margin-left: 0; }
  .practice-break { flex-basis: 100%; height: 0; }
</style>
</head>
<body>

  <section class="card card-front" aria-label="Business card front">
    <header class="front-header">
      <div class="brand">
        <span class="brand-mark"></span>
        <span class="brand-divider"></span>
        <span class="brand-name">
          <span class="line-top">Law Offices</span>
          <span class="line-bottom">of Colin Matheny</span>
        </span>
      </div>
    </header>
    <div class="front-body">
      <h1 class="person-name">Colin Matheny</h1>
      <p class="person-role">Attorney</p>
      <ul class="contact-list">
        <li>
          <svg viewBox="0 0 24 24" aria-hidden="true"><path d="M6.6 10.8a15.2 15.2 0 0 0 6.6 6.6l2.2-2.2a1 1 0 0 1 1-.25 11.4 11.4 0 0 0 3.6.57 1 1 0 0 1 1 1V20a1 1 0 0 1-1 1A17 17 0 0 1 3 4a1 1 0 0 1 1-1h3.5a1 1 0 0 1 1 1c0 1.25.2 2.45.57 3.6a1 1 0 0 1-.25 1z"/></svg>
          561-555-0148
        </li>
        <li>
          <svg viewBox="0 0 24 24" aria-hidden="true"><path d="M3 8h3V3h10l3 3v2h2v13H3zm5-3v5h9V7h-2V5zM6 12v2h2v-2zm4 0v2h2v-2zm4 0v2h2v-2zm-8 4v2h2v-2zm4 0v2h2v-2zm4 0v2h2v-2z"/></svg>
          561-555-0193
        </li>
        <li>
          <svg viewBox="0 0 24 24" aria-hidden="true"><path d="M2 5h20v14H2zm2 2v.4l8 5.1 8-5.1V7zm0 2.8V17h16V9.8l-8 5.1z"/></svg>
          colin@mathenylaw.com
        </li>
        <li>
          <svg viewBox="0 0 24 24" aria-hidden="true"><path d="M12 2a10 10 0 1 0 0 20 10 10 0 0 0 0-20zm0 2c.9 1.2 1.6 2.5 2 4h-4c.4-1.5 1.1-2.8 2-4zM4.3 14a8 8 0 0 1 0-4h3.4a16 16 0 0 0 0 4zm5.4 0a14 14 0 0 1 0-4h4.6a14 14 0 0 1 0 4zm6.6 0a16 16 0 0 0 0-4h3.4a8 8 0 0 1 0 4zM12 20c-.9-1.2-1.6-2.5-2-4h4c-.4 1.5-1.1 2.8-2 4z"/></svg>
          www.mathenylaw.com
        </li>
        <li class="contact-address">118B Coral Avenue Palm Beach, Florida 33480</li>
      </ul>
    </div>
  </section>

  <section class="card card-back" aria-label="Business card back">
    <p class="back-tagline">Over 25 Years of Experience</p>
    <div class="back-band">
      <div class="brand">
        <span class="brand-mark"></span>
        <span class="brand-divider"></span>
        <span class="brand-name">
          <span class="line-top">Law Offices</span>
          <span class="line-bottom">of Colin Matheny</span>
        </span>
      </div>
    </div>
    <ul class="practice-areas">
      <li>Civil Litigation</li>
      <li>Corporate Law</li>
      <li class="practice-break" aria-hidden="true"></li>
      <li>Business Governance</li>
      <li>Real Estate Law</li>
    </ul>
  </section>

</body>
</html>
```